Ridgeline Journeys business card

please see website
www.ridgelinejourneys.comau

info needed on card
Curtis Halvey
Ph
email
Adventure Riding GPS trails

please use my logo and colours off my site

Curtis Halvey
curtis@ridgelinejourneys.com

```html
<!DOCTYPE html>
<html lang="en">
<head>
<meta charset="utf-8">
<title>Ridgeline Journeys – Business Card</title>
<link rel="stylesheet" href="https://fonts.googleapis.com/css2?family=PT+Sans:ital,wght@0,400;0,700;1,400;1,700&display=swap">
<style>
  :root {
    --page-bg: #e7e3dd;
    --card-top: #f1f1ef;
    --card-top-edge: #dcdcd8;
    --band-dark: #0d0d0d;
    --band-mid: #2a2a2a;
    --logo-ink: #141414;
    --accent-gold: #e3bd1f;
    --icon-gold: #d9a81c;
    --text-light: #e9e9e9;
    --tagline-grey: #b8b8b8;
    --tagline-rose: #b59a9c;
    --disc-grey: #cfcfcf;
  }
  * { margin: 0; padding: 0; box-sizing: border-box; }
  html, body {
    width: 1200px;
    height: 969px;
    overflow: hidden;
    background: var(--page-bg);
    font-family: "PT Sans", sans-serif;
  }
  .business-card {
    position: absolute;
    left: 100px;
    top: 200px;
    width: 1000px;
    height: 570px;
    overflow: hidden;
    border: 1px solid var(--card-top-edge);
    box-shadow: 0 10px 30px rgba(0,0,0,0.18);
  }
  .brand-panel {
    position: absolute;
    inset: 0 0 288px 0;
    background: linear-gradient(180deg, #f7f7f5 0%, var(--card-top) 100%);
  }
  .brand-mark {
    position: absolute;
    left: 76px;
    top: 70px;
    width: 140px;
    height: 140px;
    border-radius: 50%;
    background: var(--accent-gold);
  }
  .brand-name {
    position: absolute;
    left: 240px;
    top: 92px;
    font-weight: 700;
    font-size: 44px;
    line-height: 46px;
    color: var(--logo-ink);
    text-transform: uppercase;
    letter-spacing: 0.5px;
  }
  .contact-band {
    position: absolute;
    left: 0;
    right: 0;
    bottom: 0;
    height: 288px;
    background: linear-gradient(90deg, var(--band-dark) 0%, var(--band-mid) 55%, var(--band-dark) 100%);
  }
  .band-disc {
    position: absolute;
    left: 650px;
    top: 36px;
    width: 230px;
    height: 230px;
    border-radius: 50%;
    background: var(--disc-grey);
    opacity: 0.85;
  }
  .holder-name {
    position: absolute;
    left: 60px;
    top: 28px;
    font-size: 34px;
    font-weight: 400;
    color: var(--accent-gold);
  }
  .contact-list {
    position: absolute;
    left: 60px;
    top: 96px;
    list-style: none;
  }
  .contact-item {
    display: flex;
    align-items: center;
    height: 39px;
    font-size: 23px;
    color: var(--text-light);
  }
  .contact-icon {
    width: 22px;
    height: 22px;
    margin-right: 16px;
    fill: var(--icon-gold);
  }
  .tagline {
    position: absolute;
    left: 60px;
    top: 222px;
    font-size: 25px;
    font-style: italic;
    font-weight: 700;
    color: var(--tagline-rose);
  }
  .tagline-lead { color: var(--tagline-grey); }
</style>
</head>
<body>
  <div class="business-card">
    <section class="brand-panel">
      <div class="brand-mark" aria-hidden="true"></div>
      <div class="brand-name">Ridgeline<br>Journeys</div>
    </section>
    <section class="contact-band">
      <div class="band-disc" aria-hidden="true"></div>
      <h1 class="holder-name">Curtis Halvey</h1>
      <ul class="contact-list">
        <li class="contact-item">
          <svg class="contact-icon" viewBox="0 0 24 24" aria-hidden="true"><path d="M6.6 10.8a15.1 15.1 0 0 0 6.6 6.6l2.2-2.2c.3-.3.7-.4 1-.2 1.1.4 2.3.6 3.6.6.6 0 1 .4 1 1V20c0 .6-.4 1-1 1A17 17 0 0 1 3 4c0-.6.4-1 1-1h3.5c.6 0 1 .4 1 1 0 1.3.2 2.5.6 3.6.1.3 0 .7-.2 1z"/></svg>
          612 555 0148
        </li>
        <li class="contact-item">
          <svg class="contact-icon" viewBox="0 0 24 24" aria-hidden="true"><path d="M2 5h20v14H2z M3 6l9 7 9-7" fill="none" stroke="#d9a81c" stroke-width="0"/><path d="M2 5h20v2l-10 7L2 7z"/><path d="M2 9l10 7 10-7v10H2z"/></svg>
          curtis@ridgelinejourneys.com
        </li>
        <li class="contact-item">
          <svg class="contact-icon" viewBox="0 0 24 24" aria-hidden="true"><path d="M12 2a10 10 0 1 0 0 20 10 10 0 0 0 0-20zm-1 17.9A8 8 0 0 1 4.1 11H7c.3 0 1 .5 1 1v1c0 1 1 2 2 2v3.9zm6.9-2.5c-.3-.8-1-1.4-1.9-1.4h-1v-3c0-.6-.4-1-1-1H8v-2h2c.6 0 1-.4 1-1V7h2a2 2 0 0 0 2-2v-.4a8 8 0 0 1 2.9 12.8z"/></svg>
          www.ridgelinejourneys.com.au
        </li>
      </ul>
      <p class="tagline"><span class="tagline-lead">Adventure</span> Riding GPS trails</p>
    </section>
  </div>
</body>
</html>
```